Design of a promotional offer flyer required to promote low-cost websites to 1-man band businesses

I want a flyer designed - either a double-sided A5 flyer or even A4 folded into a third double-sided. The flyer is to showcase a new service - low-cost websites for 1-man-band businesses, business startups and tradesmen in England. Look at the copy, find some pix and let me know! Flyer will be printed and used as an image on my website too. Pix could be related to some of the target groups. We need to stress the simple message that websites start from £5 per week and this is an-all-in-one fee.

Target Market(s)

Tradesmen, business start ups and 1-man band businesses that want a website

Industry/Entity Type

Small Business

Contact Information for Business Card

All contact details and name of business to be confirmed shortly

Font styles to use
Serif

Requirements
Must have
• Basic messages from copy for flyer i.e. websites from £5 per week and what each client gets for that price to be included on the business card! Please read copy for the flyer.
Nice to have
• Nice background image or series of small images relevant to the target audience. Again, see list of targets from copy for flyer.
Should not have
• I don't want exact or similar design to my main business Blue Harbour Promotions. The new flyer and business card should be a different and distinct branding to that of Blue Harbour Promotions. Aimed at a more economical style, whilst looking professional, but relevant to the target audiences.

```html
<!DOCTYPE html>
<html lang="en">
<head>
<meta charset="utf-8">
<title>Solo Trade Websites – Flyer</title>
<link href="https://fonts.googleapis.com/css2?family=Oswald:wght@300;400;500;700&family=Lato:wght@400;700&family=Roboto:wght@500;700&display=swap" rel="stylesheet">
<style>
  :root{
    --stage:#c0c0c0;
    --paper:#ffffff;
    --red:#e8100f;
    --red-deep:#c8070a;
    --yellow:#ffec00;
    --ink:#222222;
    --grey-ink:#4a4a4a;
    --black:#111111;
    --strip:#333333;
    --promo-red:#e21a22;
  }
  *{box-sizing:border-box;margin:0;padding:0}
  html,body{width:1200px;height:1200px;overflow:hidden;background:var(--stage)}
  .canvas{position:relative;width:1200px;height:1200px;background:var(--stage)}
  .page{position:absolute;top:218px;width:523px;height:734px;background:var(--paper);overflow:hidden}
  .page--front{left:53px}
  .page--back{left:630px}
  .abs{position:absolute}

  /* front */
  .hero-photo{left:0;top:0;width:523px;height:392px}
  .brand{left:32px;top:26px;font-family:'Roboto',sans-serif}
  .brand__top{font-size:35px;font-weight:500;color:var(--grey-ink);line-height:1}
  .brand__main{font-size:56px;font-weight:700;color:var(--red);line-height:1;margin-top:4px}
  .headline{left:0;width:523px;top:388px;text-align:center;font-family:'Oswald',sans-serif;font-weight:700;text-transform:uppercase;line-height:1}
  .headline__big{font-size:43px;color:var(--red-deep)}
  .headline__sub{font-size:31px;color:var(--grey-ink);margin-top:6px}
  .price-band{left:0;top:485px;width:523px;height:95px;background:linear-gradient(90deg,var(--red) 0%,var(--red-deep) 100%)}
  .price-band__lead{left:38px;top:14px;width:226px;font-family:'Oswald',sans-serif;font-weight:300;font-size:18.5px;line-height:21px;color:#fff}
  .price-band__lead b{font-weight:500}
  .price-band__divider{left:271px;top:8px;width:1.5px;height:80px;background:#fff}
  .price-band__offer{left:287px;top:6px;font-family:'Oswald',sans-serif;font-weight:700;color:var(--yellow);line-height:1}
  .price-band__amount{font-size:43px}
  .price-band__note{font-size:24px;margin-top:4px}
  .audience{left:0;top:580px;width:523px;height:77px;background:var(--black);color:#fff;font-family:'Lato',sans-serif;font-size:11.6px;line-height:14.5px;padding:9px 46px 0 42px;text-align:center}
  .rule-red{left:0;top:657px;width:523px;height:4px;background:var(--red)}
  .address-strip{left:0;top:661px;width:523px;height:33px;display:flex;align-items:center;justify-content:center;font-family:'Lato',sans-serif;font-size:11.8px;color:var(--ink)}
  .web-strip{left:0;top:694px;width:523px;height:40px;background:var(--black);display:flex;align-items:center;justify-content:center;font-family:'Lato',sans-serif;font-size:11px;letter-spacing:2.2px;color:#fff}

  /* back */
  .top-band{left:0;top:0;width:523px;height:25px;background:var(--red)}
  .back-photo{left:266px;top:34px;width:236px;height:204px}
  .benefits-title{left:30px;top:38px;font-family:'Oswald',sans-serif;font-weight:700;font-size:32px;color:var(--ink);line-height:1}
  .benefits{left:34px;top:85px;width:470px;list-style:none;font-family:'Lato',sans-serif;font-size:12px;line-height:14.4px;color:var(--ink)}
  .benefits li{position:relative;padding-left:20px;margin-bottom:4.8px}
  .benefits li svg{position:absolute;left:0;top:2px;width:11px;height:11px}
  .benefits .narrow{width:210px}
  .fee-intro{left:0;top:362px;width:335px;text-align:center;font-family:'Roboto',sans-serif;font-weight:500;font-size:17.5px;color:var(--ink)}
  .fee-band{left:0;top:390px;width:320px;height:46px;background:var(--yellow);font-family:'Lato',sans-serif;font-size:14.4px;line-height:19px;color:#e2241c;text-align:center;padding-top:4px}
  .fee-band span{color:var(--ink)}
  .devices{left:322px;top:358px;width:180px;height:110px}
  .promo-title{left:0;top:459px;width:400px;text-align:center;font-family:'Roboto',sans-serif;font-weight:700;font-size:24px;letter-spacing:1px;color:var(--promo-red)}
  .painter-photo{left:376px;top:470px;width:147px;height:237px}
  .promo-box{left:26px;top:490px;width:351px;height:95px;border:2px solid var(--ink);background:#fff;text-align:center;font-family:'Oswald',sans-serif}
  .promo-box__line{font-size:14.5px;font-weight:500;color:var(--ink);line-height:21px}
  .promo-box__line:first-child{margin-top:8px}
  .promo-box mark{background:var(--yellow);color:var(--promo-red);padding:0 3px}
  .promo-box__cost{font-size:27px;font-weight:500;color:var(--promo-red);line-height:1;margin-top:4px}
  .contact{left:0;top:623px;width:375px;height:84px;background:var(--red-deep);color:#fff;text-align:center;font-family:'Lato',sans-serif;font-weight:700;font-size:12px;line-height:16px}
  .contact__phone{font-family:'Oswald',sans-serif;font-size:23px;font-weight:500;line-height:1;padding-top:7px;margin-bottom:3px}
  .contact__detail span{font-weight:400}
  .bottom-strip{left:0;top:707px;width:523px;height:27px;background:var(--strip)}
</style>
</head>
<body>
<div class="canvas">

  <!-- Front page -->
  <section class="page page--front">
    <svg class="abs hero-photo" viewBox="0 0 523 392" role="img" aria-label="Photo of a smiling woman pointing at a laptop screen showing a phone and floating app icons">
      <defs>
        <linearGradient id="heroTone" x1="0" y1="0" x2="1" y2="1">
          <stop offset="0" stop-color="#f1ece8"/>
          <stop offset="0.55" stop-color="#d9cbc1"/>
          <stop offset="1" stop-color="#b9c7d6"/>
        </linearGradient>
      </defs>
      <path d="M285 18 H510 V390 H58 V205 H285 Z" fill="url(#heroTone)"/>
    </svg>

    <div class="abs brand">
      <div class="brand__top">Solo Trade</div>
      <div class="brand__main">Websites</div>
    </div>

    <h1 class="abs headline">
      <div class="headline__big">Want a website</div>
      <div class="headline__sub">without it costing the earth?</div>
    </h1>

    <div class="abs price-band">
      <p class="abs price-band__lead">Professionally-designed websites for <b>tradesmen, business start-ups</b> and <b>1-man bands</b> from only</p>
      <div class="abs price-band__divider"></div>
      <div class="abs price-band__offer">
        <div class="price-band__amount">£5 per week</div>
        <div class="price-band__note">&amp; NO upfront costs!</div>
      </div>
    </div>

    <p class="abs audience">Suitable for plumbers, electricians, roofers, builders, painters and decorators, joiners, business start-ups, 1-man bands such as hairdressers, photographers, fitness instructors, window cleaners, beauticians, gardeners, odd job men, wheelie bin cleaners, IFAs or self-employed consultants.</p>

    <div class="abs rule-red"></div>
    <p class="abs address-strip">ADDRESS: 27 Kestrel Road, Bolton, BL9 4XT, Lancashire.</p>
    <p class="abs web-strip">www.solotradewebsites.co.uk</p>
  </section>

  <!-- Back page -->
  <section class="page page--back">
    <div class="abs top-band"></div>

    <svg class="abs back-photo" viewBox="0 0 236 204" role="img" aria-label="Photo of a smiling woman holding an open laptop showing a website template">
      <defs>
        <linearGradient id="backTone" x1="0" y1="0" x2="1" y2="1">
          <stop offset="0" stop-color="#f4efec"/>
          <stop offset="0.6" stop-color="#d8c8bf"/>
          <stop offset="1" stop-color="#9aa3ad"/>
        </linearGradient>
      </defs>
      <rect width="236" height="204" fill="url(#backTone)"/>
    </svg>

    <h2 class="abs benefits-title">Here’s what you get :</h2>

    <ul class="abs benefits">
      <li class="narrow"><svg viewBox="0 0 12 12"><path d="M1 6.5 L4.5 10 L11 1.5" fill="none" stroke="#e8100f" stroke-width="2.2"/></svg>Professionally-designed 1-page or 5-page website (Home, About Us, Services, Contact Us, News)</li>
      <li class="narrow"><svg viewBox="0 0 12 12"><path d="M1 6.5 L4.5 10 L11 1.5" fill="none" stroke="#e8100f" stroke-width="2.2"/></svg>Responsive design that displays properly on mobiles and tablets</li>
      <li><svg viewBox="0 0 12 12"><path d="M1 6.5 L4.5 10 L11 1.5" fill="none" stroke="#e8100f" stroke-width="2.2"/></svg>On-going changes and updates</li>
      <li><svg viewBox="0 0 12 12"><path d="M1 6.5 L4.5 10 L11 1.5" fill="none" stroke="#e8100f" stroke-width="2.2"/></svg>All text written for you</li>
      <li><svg viewBox="0 0 12 12"><path d="M1 6.5 L4.5 10 L11 1.5" fill="none" stroke="#e8100f" stroke-width="2.2"/></svg>Photographs (Royalty-free stock images)</li>
      <li><svg viewBox="0 0 12 12"><path d="M1 6.5 L4.5 10 L11 1.5" fill="none" stroke="#e8100f" stroke-width="2.2"/></svg>Professional email addresses e.g. info@yourcompany.co.uk, sales@yourcompany.co.uk and yourname@yourcompany.co.uk. We’ll even set up these email addresses on your PC and laptop!</li>
      <li><svg viewBox="0 0 12 12"><path d="M1 6.5 L4.5 10 L11 1.5" fill="none" stroke="#e8100f" stroke-width="2.2"/></svg>Links to your social media accounts</li>
      <li><svg viewBox="0 0 12 12"><path d="M1 6.5 L4.5 10 L11 1.5" fill="none" stroke="#e8100f" stroke-width="2.2"/></svg>Up to 1 hour's changes each month to content, pix, and adding new pages</li>
      <li><svg viewBox="0 0 12 12"><path d="M1 6.5 L4.5 10 L11 1.5" fill="none" stroke="#e8100f" stroke-width="2.2"/></svg>Professional hosting for your website and email</li>
      <li><svg viewBox="0 0 12 12"><path d="M1 6.5 L4.5 10 L11 1.5" fill="none" stroke="#e8100f" stroke-width="2.2"/></svg>No upfront cost! Just weekly, monthly or annual invoice - you choose!</li>
    </ul>

    <p class="abs fee-intro">For an all-in fee from</p>
    <p class="abs fee-band">only £5 per week for a 1-page website<br><span>or</span> £10 per week for a 5-page website.</p>

    <svg class="abs devices" viewBox="0 0 180 110" role="img" aria-label="Illustration of a website shown on desktop, laptop, tablet and phone screens">
      <defs>
        <linearGradient id="deviceTone" x1="0" y1="0" x2="0" y2="1">
          <stop offset="0" stop-color="#3b4149"/>
          <stop offset="1" stop-color="#c9ced4"/>
        </linearGradient>
      </defs>
      <rect x="0" y="0" width="180" height="110" fill="url(#deviceTone)" opacity="0.55"/>
    </svg>

    <h3 class="abs promo-title">Promotional Offer :</h3>

    <svg class="abs painter-photo" viewBox="0 0 147 237" role="img" aria-label="Photo of a decorator in white overalls painting a wall with a roller">
      <defs>
        <linearGradient id="painterTone" x1="0" y1="0" x2="0" y2="1">
          <stop offset="0" stop-color="#ffffff"/>
          <stop offset="0.5" stop-color="#f3e6d6"/>
          <stop offset="1" stop-color="#e6d3bd"/>
        </linearGradient>
      </defs>
      <rect width="147" height="237" fill="url(#painterTone)"/>
    </svg>

    <div class="abs promo-box">
      <p class="promo-box__line">Order your new 5-page website <mark>before 31st July 2017</mark></p>
      <p class="promo-box__line">and we’ll set up a Friendbook Business Page for FREE.</p>
      <p class="promo-box__cost">Normal Cost: £97 plus VAT!</p>
    </div>

    <div class="abs contact">
      <p class="contact__phone">Call: &nbsp;01632 960 418</p>
      <p class="contact__detail">EMAIL: <span>info@solotradewebsites.co.uk</span></p>
      <p class="contact__detail">Address: <span>27 Kestrel Road, Bolton, BL9 4XT, Lancashire.</span></p>
      <p class="contact__detail">Visit our web : <span>www.solotradewebsites.co.uk</span></p>
    </div>

    <div class="abs bottom-strip"></div>
  </section>

</div>
</body>
</html>
```